Flyers

Modify Existing Flyer and create another for exterior company
Updates

Previous Brief has been updated- we want to update this existing one also

Target Market(s)

Exterior Remodeling Customers

Industry/Entity Type

Remodeling/Construction

```html
<!DOCTYPE html>
<html lang="en">
<head>
<meta charset="utf-8">
<title>Crestline Roofing and Exteriors Flyer</title>
<link href="https://fonts.googleapis.com/css2?family=Poppins:wght@400;500;600;700&display=swap" rel="stylesheet">
<style>
:root{
  --navy:#0c1428;
  --blue:#1a7fd0;
  --orange:#e8541c;
  --ink:#1d1d24;
  --paper:#f6f6f7;
  --stage:#ececec;
  --rule:#c9c9cf;
}
*{box-sizing:border-box;margin:0;padding:0}
html,body{width:1200px;height:2767px;overflow:hidden;background:var(--stage);font-family:'Poppins',sans-serif;color:var(--ink)}
.flyer{position:absolute;left:60px;top:618px;width:1080px;height:1530px;background:var(--paper);overflow:hidden;box-shadow:0 10px 30px rgba(0,0,0,.18)}
.top-band{position:absolute;left:0;top:0;width:100%;height:222px;background:var(--navy)}
.side-strip{position:absolute;top:225px;width:52px;height:38px;background:var(--blue)}
.side-strip.left{left:0}.side-strip.right{right:0}
.brand{position:absolute;left:0;top:36px;width:100%;text-align:center;color:#fff;font-weight:600}
.brand-name{font-size:46px;line-height:52px;letter-spacing:3px}
.brand-tag{font-size:15px;letter-spacing:1px;line-height:22px}
.hero{position:absolute;left:52px;top:147px;width:980px;height:263px;border:5px solid #fff;background:#fff}
.hero svg{display:block}
.headline{position:absolute;left:0;width:100%;text-align:center;font-weight:600;text-transform:uppercase}
.headline.one{top:414px;font-size:45px;color:#2a2a30;line-height:56px}
.headline.two{top:460px;font-size:52px;color:var(--blue);font-weight:700;line-height:60px}
.locale-bar{position:absolute;left:73px;top:518px;width:770px;height:36px;background:var(--orange);color:#fff;font-weight:600;font-size:21px;line-height:36px;padding-left:16px;clip-path:polygon(0 0,100% 0,98% 100%,0 100%)}
.locale-pill{position:absolute;left:838px;top:518px;width:174px;height:36px;background:var(--navy);color:#fff;font-weight:600;font-size:17px;line-height:36px;padding-left:44px;clip-path:polygon(3% 0,100% 0,100% 100%,0 100%)}
.locale-pill svg{position:absolute;left:20px;top:8px}
.service{position:absolute}
.service-title{font-size:35px;font-weight:500;line-height:40px;white-space:nowrap;color:var(--ink)}
.service-title span{color:var(--blue)}
.service-text{font-size:14.5px;font-weight:500;line-height:18px;margin-top:6px}
.ticks{list-style:none;display:flex;flex-wrap:wrap;font-size:14px;line-height:22px;margin-top:6px}
.ticks li{position:relative;padding-left:22px}
.ticks li::before{content:"";position:absolute;left:0;top:6px;width:10px;height:10px;border:1.5px solid var(--orange);border-radius:50%}
.ticks li::after{content:"";position:absolute;left:4px;top:8px;width:3px;height:5px;border:solid var(--orange);border-width:0 1.5px 1.5px 0;transform:rotate(40deg)}
.icon{position:absolute}
.photo{position:absolute}
.divider{position:absolute;left:73px;width:937px;border-top:1.5px dashed var(--rule)}
.footer{position:absolute;left:0;top:1433px;width:100%;height:97px;background:var(--blue)}
.footer-call{position:absolute;left:0;top:0;width:430px;height:97px;background:var(--orange);clip-path:polygon(0 0,100% 0,94% 100%,0 100%);color:#fff;padding:10px 0 0 72px}
.footer-call .small{font-size:27px;font-weight:500;line-height:30px}
.footer-call .big{font-size:41px;font-weight:700;line-height:44px}
.contacts{position:absolute;left:440px;right:50px;top:0;height:97px;display:flex;align-items:center;justify-content:space-between}
.contact{color:#fff;font-weight:500;font-size:30px;line-height:40px;white-space:nowrap}
.contact svg{vertical-align:-3px;margin-right:8px}
</style>
</head>
<body>
<main class="flyer">
  <div class="top-band"></div>
  <div class="side-strip left"></div>
  <div class="side-strip right"></div>

  <header class="brand">
    <div class="brand-name">CRESTLINE</div>
    <div class="brand-tag">ROOFING AND EXTERIORS</div>
  </header>

  <section class="hero">
    <svg width="970" height="253" viewBox="0 0 970 253">
      <defs>
        <linearGradient id="roofTone" x1="0" y1="0" x2="1" y2="1">
          <stop offset="0" stop-color="#b9c3c9"/><stop offset=".5" stop-color="#4d5870"/><stop offset="1" stop-color="#7f8f5a"/>
        </linearGradient>
        <linearGradient id="exteriorTone" x1="0" y1="0" x2="1" y2="1">
          <stop offset="0" stop-color="#d9dde0"/><stop offset=".5" stop-color="#7a5a44"/><stop offset="1" stop-color="#4f6a3a"/>
        </linearGradient>
      </defs>
      <g role="img" aria-label="House roof fitted with solar panels">
        <polygon points="0,0 510,0 430,253 0,253" fill="url(#roofTone)"/>
      </g>
      <g role="img" aria-label="Modern timber-clad house exterior with terrace">
        <polygon points="518,0 970,0 970,253 438,253" fill="url(#exteriorTone)"/>
      </g>
      <polygon points="0,203 446,203 430,253 0,253" fill="rgba(20,26,40,.8)"/>
      <polygon points="454,203 970,203 970,253 438,253" fill="#c24a14"/>
      <text x="210" y="241" text-anchor="middle" fill="#fff" font-family="Poppins, sans-serif" font-weight="700" font-size="33">ROOFING</text>
      <text x="710" y="241" text-anchor="middle" fill="#fff" font-family="Poppins, sans-serif" font-weight="700" font-size="33">EXTERIORS</text>
    </svg>
  </section>

  <h1 class="headline one">Ready for a beautiful and functional</h1>
  <h2 class="headline two">Roofing and Exteriors</h2>

  <div class="locale-bar">WORK WITH A TOP-RATED LOCAL REMODELING COMPANY IN</div>
  <div class="locale-pill">
    <svg width="18" height="20" viewBox="0 0 18 20" fill="none" stroke="#fff" stroke-width="1.8"><path d="M9 12s5-4 5-7.5A5 5 0 0 0 4 4.5C4 8 9 12 9 12z"/><circle cx="9" cy="4.8" r="1.8"/><path d="M3 14l-2 5h16l-2-5"/></svg>
    ANKENY, IA
  </div>

  <svg class="icon" style="left:73px;top:597px" width="44" height="38" viewBox="0 0 44 38" fill="none" stroke="var(--blue)" stroke-width="2"><path d="M2 14l20-11 20 11"/><rect x="6" y="14" width="32" height="22"/><path d="M6 22h32M6 29h32M16 14v22M28 14v22" stroke="var(--orange)"/></svg>
  <div class="service" style="left:127px;top:591px;width:500px">
    <div class="service-title">ROOFING <span>SERVICES</span></div>
    <p class="service-text">Regardless of the time of day, we're committed to providing you with an immediate response to all roofing emergencies.</p>
    <ul class="ticks" style="width:440px">
      <li style="width:210px">Roof Repair</li><li>Roof Maintenance</li>
      <li style="width:210px">Roof Replacements</li><li>Soffit, Fascia &amp; Gutters</li>
      <li style="width:210px">Roof &amp; Attic Ventilation</li><li>Skylights &amp; Sun Tunnels</li>
    </ul>
  </div>
  <div class="photo" role="img" aria-label="Modern house with dark metal roof among palm trees" style="left:682px;top:587px;width:328px;height:185px;background:linear-gradient(160deg,#e9eef2 0%,#6d8596 35%,#283a63 60%,#8f7a5c 85%,#5f7446 100%)"></div>
  <div class="divider" style="top:793px"></div>

  <div class="photo" role="img" aria-label="Tropical home with wooden deck and lounge seating" style="left:73px;top:803px;width:328px;height:184px;background:linear-gradient(180deg,#3b86c9 0%,#8ab6d8 35%,#8a5a3a 60%,#3f3128 100%)"></div>
  <svg class="icon" style="left:420px;top:840px" width="42" height="40" viewBox="0 0 42 40" fill="none" stroke="var(--blue)" stroke-width="2"><rect x="14" y="4" width="20" height="34"/><rect x="3" y="16" width="11" height="22"/><path d="M19 10h4M26 10h4M19 17h4M26 17h4M19 24h4M26 24h4" stroke="var(--orange)"/><path d="M1 38h40"/></svg>
  <div class="service" style="left:474px;top:835px;width:540px">
    <div class="service-title">HOME <span>EXTERIORS</span></div>
    <p class="service-text">Siding can transform your home's curb appeal, improve its functionality and protection, and increase the value of your property.</p>
    <ul class="ticks">
      <li style="margin-right:18px">Siding &amp; Stucco</li><li style="margin-right:18px">Windows &amp; Doors</li><li>Exterior Remodeling</li>
    </ul>
  </div>
  <div class="divider" style="top:998px"></div>

  <svg class="icon" style="left:73px;top:1035px" width="46" height="42" viewBox="0 0 46 42" fill="none" stroke="var(--blue)" stroke-width="2"><path d="M6 14a15 11 0 0 1 30 0z" stroke="var(--orange)"/><path d="M21 14v26M4 28h34M8 28v12M34 28v12M2 40h42"/></svg>
  <div class="service" style="left:130px;top:1037px;width:560px">
    <div class="service-title">DECKS/<span>PATIOS</span></div>
  </div>
  <div class="service" style="left:80px;top:1081px;width:560px">
    <p class="service-text">An outdoor space is a great addition to any residential property. When you decide to build a patio or deck, you'll be able to experience a variety of benefits. Your outdoor area will increase your :</p>
    <ul class="ticks" style="margin-left:-8px">
      <li style="margin-right:14px">Property value</li><li style="margin-right:14px">Curb appeal</li><li>Functional living space</li>
    </ul>
  </div>
  <div class="photo" role="img" aria-label="Poolside patio with lounge chairs and parasols" style="left:681px;top:1007px;width:328px;height:185px;background:linear-gradient(180deg,#cfd4cf 0%,#8f8a78 40%,#5c6a4c 65%,#6d7f80 100%)"></div>
  <div class="divider" style="top:1203px"></div>

  <div class="photo" role="img" aria-label="Bright bedroom with large windows" style="left:73px;top:1218px;width:328px;height:184px;background:linear-gradient(180deg,#d8cdbd 0%,#a89276 40%,#5e4b3c 70%,#e7e0d6 100%)"></div>
  <svg class="icon" style="left:460px;top:1224px" width="46" height="44" viewBox="0 0 46 44" fill="none" stroke-width="2"><path d="M3 22L20 6l17 16" stroke="var(--orange)"/><path d="M8 18v22h24V18" stroke="var(--blue)"/><rect x="15" y="26" width="10" height="14" stroke="var(--blue)"/><path d="M32 30h12v10H32" stroke="var(--blue)"/></svg>
  <div class="service" style="left:516px;top:1220px;width:500px">
    <div class="service-title">HOME <span>ADDITIONS</span></div>
    <p class="service-text">No matter what kind of space you need, our team will bring your vision to life. You can hire us if you need a :</p>
  </div>
  <ul class="ticks service" style="left:516px;top:1313px;width:460px;line-height:24px">
    <li style="width:214px">Bathroom addition</li><li>Guest room addition</li>
    <li style="width:214px">Bedroom addition</li><li>Living room addition</li>
    <li style="width:214px">Garage addition</li><li>Sunroom addition</li>
    <li style="width:214px">Basement addition</li>
  </ul>

  <footer class="footer">
    <div class="footer-call">
      <div class="small">CALL TODAY FOR YOUR</div>
      <div class="big">FREE ESTIMATE</div>
    </div>
    <div class="contacts">
      <div class="contact">
        <svg width="24" height="24" viewBox="0 0 24 24" fill="none" stroke="#fff" stroke-width="2"><path d="M5 3l4 1 1 5-2 2a12 12 0 0 0 5 5l2-2 5 1 1 4-3 2C10 21 3 14 3 6z"/><path d="M15 3a6 6 0 0 1 6 6M15 7a2 2 0 0 1 2 2"/></svg>555-014-2870
      </div>
      <div class="contact">
        <svg width="24" height="24" viewBox="0 0 24 24" fill="none" stroke="#fff" stroke-width="2"><circle cx="12" cy="12" r="10"/><path d="M2 12h20M12 2c3 3 3 17 0 20M12 2c-3 3-3 17 0 20"/></svg>www.crestiowa.com
      </div>
    </div>
  </footer>
</main>
</body>
</html>
```